A new updated business card. A good first impression for new customers to our business.

I need something unique. I will attached a picture of our old rubbish cards, and also our current Logo ( I think this needs an update if you have any ideas, its very basic and budget)The best way you will get to see my business is checking our Facebook page, I don't really know what else to say, but anything you want to know, ask away.www.facebook.com/tkwashandseal/

Target Market(s)

Home owners

Industry/Entity Type

Business

Contact Information for Business Card

T&K's Pressure Cleaning & Concrete Sealing
Maya 0492 615 370 maya@tkwashandseal.com
Dylan 0431 528 906 dylan@tkwashandseal.com

FB: www.facebook.com/tkwashandseal/
Website: www.tkwashandseal.net (This is pretty rubbish- we don't really use it)

100% customer satisfaction guaranteed

All aspects of Hi-Pressure Cleaning
Sealing & Re-Sealing
Roof Cleaning
Colour sealing
Decorative coatings

Free no obligation quotes

Requirements
Must have
• NO OBLIGATION FREE quotes
• 100% Customer satisfaction guaranteed
• Can you please add both names, contact details and email address on one card.
• Dylan 0431 528 906
• dylan@tkwashandseal.com
• Maya 0492 615 370
• maya@tkwashandseal.com
• Please change the services:
• Hot/Cold Hi-Pressure Cleaning
• Sealing & Re-Sealing
• Roof Cleaning
• Colour Sealing
• Decorative Coatings
• Concrete Honing
• Thanks
Nice to have
• Something a bit different, something eye catching.l

```html
<!DOCTYPE html>
<html lang="en">
<head>
<meta charset="utf-8">
<title>T&amp;K's Pressure Cleaning &amp; Concrete Sealing – Business Card</title>
<link rel="stylesheet" href="https://fonts.googleapis.com/css2?family=Roboto+Condensed:wght@400;700&family=Yellowtail&display=swap">
<style>
  :root {
    --card-black: #141414;
    --brand-red: #e8141c;
    --white: #ffffff;
    --quote-grey: #3b3b3b;
    --bg-light: #b9b9b9;
    --bg-dark: #7d7d7d;
  }
  * { box-sizing: border-box; margin: 0; padding: 0; }
  html, body { width: 1200px; height: 960px; overflow: hidden; }
  body {
    background: radial-gradient(ellipse at 50% 40%, var(--bg-light), var(--bg-dark));
    font-family: "Roboto Condensed", Arial, sans-serif;
    color: var(--white);
    position: relative;
  }
  .card {
    position: absolute;
    top: 315px;
    width: 540px;
    height: 330px;
    background: var(--card-black);
    overflow: hidden;
    box-shadow: 0 14px 30px rgba(0,0,0,0.35);
  }
  .card--services { left: 40px; }
  .card--contact { left: 620px; }

  .band {
    position: absolute;
    left: 0; right: 0;
    background: var(--brand-red);
    display: flex;
    align-items: center;
  }
  .website {
    font-weight: 700;
    color: var(--white);
    letter-spacing: 0.2px;
  }

  /* Services side */
  .card--services .brand {
    position: absolute;
    top: 34px; left: 0; right: 0;
    text-align: center;
    font-weight: 700;
    color: var(--white);
  }
  .brand-name { font-size: 46px; line-height: 1; display: block; }
  .brand-tagline { font-size: 15px; line-height: 1.25; display: block; margin-top: 4px; }
  .sectors {
    position: absolute; top: 146px; left: 0; right: 0;
    text-align: center; font-size: 22px;
  }
  .slogan {
    position: absolute; top: 172px; left: 0; right: 0;
    text-align: center; font-size: 40px; font-weight: 700; letter-spacing: 1px;
  }
  .services {
    position: absolute; top: 222px; left: 0; right: 0;
    text-align: center; font-size: 17px; line-height: 23px;
  }
  .services .dot { color: var(--brand-red); margin: 0 4px; }
  .card--services .band { top: 272px; height: 40px; justify-content: center; }
  .card--services .website { font-size: 28px; }

  /* Contact side */
  .card--contact .brand {
    position: absolute; top: 22px; left: 28px;
    font-weight: 700; color: var(--white);
  }
  .card--contact .brand-name { font-size: 40px; }
  .card--contact .brand-tagline { font-size: 14px; width: 170px; }
  .guarantee-seal {
    position: absolute; top: 128px; left: 44px;
    width: 86px; height: 86px;
  }
  .free-quotes {
    position: absolute; top: 44px; right: 0;
    width: 124px; height: 70px;
    background: var(--quote-grey);
    text-align: center; line-height: 1;
    padding-top: 6px;
  }
  .free-quotes .get { font-family: "Yellowtail", cursive; color: var(--brand-red); font-size: 30px; display: block; }
  .free-quotes .label { font-weight: 700; font-size: 17px; display: block; margin-top: 2px; }

  .contacts { position: absolute; top: 122px; left: 150px; width: 372px; }
  .person { position: relative; height: 58px; }
  .person-name {
    position: absolute; left: 0; top: -4px; width: 80px;
    text-align: right;
    font-family: "Yellowtail", cursive; color: var(--brand-red); font-size: 28px;
  }
  .divider { position: absolute; left: 88px; top: 2px; width: 1px; height: 30px; background: var(--white); }
  .phone { position: absolute; left: 98px; top: -2px; font-size: 29px; font-weight: 700; }
  .email { position: absolute; left: 60px; top: 33px; font-size: 14px; }
  .social { position: relative; height: 22px; }
  .social .handle { position: absolute; left: 44px; top: 0; font-size: 15px; }
  .icon { position: absolute; right: 0; }
  .icon--phone { top: 4px; }
  .icon--mail { top: 34px; right: 2px; }
  .card--contact .band { top: 256px; height: 46px; padding-left: 30px; }
  .card--contact .website { font-size: 30px; }
</style>
</head>
<body>

<section class="card card--services" aria-label="Business card, services side">
  <div class="brand">
    <span class="brand-name">T&amp;K's</span>
    <span class="brand-tagline">Pressure Cleaning<br>&amp; Concrete Sealing</span>
  </div>
  <p class="sectors">Residential &amp; Commercial</p>
  <p class="slogan">QUALITY EVERYTIME</p>
  <p class="services">
    Hot/Cold Hi-Pressure Cleaning<span class="dot">•</span>Sealing &amp; Re-Sealing<br>
    Roof Cleaning<span class="dot">•</span>Colour Sealing<span class="dot">•</span>Decorative Coatings<span class="dot">•</span>Concrete Honing
  </p>
  <div class="band"><span class="website">www.tkwashandseal.net</span></div>
</section>

<section class="card card--contact" aria-label="Business card, contact side">
  <div class="brand">
    <span class="brand-name">T&amp;K's</span>
    <span class="brand-tagline">Pressure Cleaning<br>&amp; Concrete Sealing</span>
  </div>

  <svg class="guarantee-seal" viewBox="0 0 86 86" role="img" aria-label="100% customer satisfaction guaranteed seal">
    <circle cx="43" cy="43" r="42" fill="var(--brand-red)"/>
  </svg>

  <div class="free-quotes">
    <span class="get">Get</span>
    <span class="label">Free Quotes</span>
  </div>

  <div class="contacts">
    <div class="person">
      <span class="person-name">Dylan</span>
      <span class="divider"></span>
      <span class="phone">0431 528 906</span>
      <span class="email">dylan@tkwashandseal.com</span>
      <svg class="icon icon--phone" width="24" height="24" viewBox="0 0 24 24" aria-hidden="true">
        <circle cx="12" cy="12" r="12" fill="var(--brand-red)"/>
        <rect x="8.5" y="6" width="7" height="12" rx="1.3" fill="none" stroke="#fff" stroke-width="1.6"/>
        <circle cx="12" cy="15.6" r="0.9" fill="#fff"/>
      </svg>
      <svg class="icon icon--mail" width="20" height="14" viewBox="0 0 20 14" aria-hidden="true">
        <rect width="20" height="14" fill="var(--brand-red)"/>
        <path d="M0 0 L10 8 L20 0" fill="none" stroke="var(--card-black)" stroke-width="1.6"/>
      </svg>
    </div>
    <div class="person">
      <span class="person-name">Maya</span>
      <span class="divider"></span>
      <span class="phone">0492 615 370</span>
      <span class="email">maya@tkwashandseal.com</span>
      <svg class="icon icon--phone" width="24" height="24" viewBox="0 0 24 24" aria-hidden="true">
        <circle cx="12" cy="12" r="12" fill="var(--brand-red)"/>
        <rect x="8.5" y="6" width="7" height="12" rx="1.3" fill="none" stroke="#fff" stroke-width="1.6"/>
        <circle cx="12" cy="15.6" r="0.9" fill="#fff"/>
      </svg>
      <svg class="icon icon--mail" width="20" height="14" viewBox="0 0 20 14" aria-hidden="true">
        <rect width="20" height="14" fill="var(--brand-red)"/>
        <path d="M0 0 L10 8 L20 0" fill="none" stroke="var(--card-black)" stroke-width="1.6"/>
      </svg>
    </div>
    <div class="social">
      <span class="handle">fb.com/tkwashandseal</span>
      <svg class="icon" width="24" height="24" viewBox="0 0 24 24" aria-hidden="true" style="top:-2px">
        <circle cx="12" cy="12" r="12" fill="var(--brand-red)"/>
      </svg>
    </div>
  </div>

  <div class="band"><span class="website">www.tkwashandseal.net</span></div>
</section>

</body>
</html>
```